Calden L - Premium Business Cards

Background of Calden L
Calden Leafworks is a cigar mobile lounge where guests become family. A place of luxury, relaxation, and ambiance is the global popularity demand. Calden Leafworks strives to provide first-class service of quality and products. Our goal is to ensure that every guest is treated and serviced as a VIP.

Calden Leafworks was founded by Dennis Markow Jr in January 2020. After 15 years of cigar reviews and research Dennis decided it was time to launch his own cigar brand and boutique cigar company. With a wealth of knowledge and years of experience Calden Leafworks was born. With opulence for all cultures, Calden Leafworks offers hand rolled cigars with premium blend tobacco from sweet to bold imported from Costa Rica, Dominican Republic, and Nicaragua. Thank you for your business!

Objective:
Create a business card template to be used for all employees. Design should communicate premium and classy. And should use earth tone colors.

Design should include:
1. Client wants to incorporate the cigar leaf
2. Logo
3. Tagline: Respect the smoke
3. Content info:
Kevin Oldacre
Owner
555-017-4863
koldacre@caldenleaf.com
caldenleafworks.com

```html
<!DOCTYPE html>
<html lang="en">
<head>
<meta charset="utf-8">
<title>Calden Leafworks – Business Cards</title>
<link href="https://fonts.googleapis.com/css2?family=Oswald:wght@500&family=Montserrat:wght@800&family=Arimo:wght@400;700&display=swap" rel="stylesheet">
<style>
  :root {
    --stage: #1c1611;
    --card-dark: #3a2a1f;
    --card-light: #f3eadb;
    --ink-dark: #33251b;
    --ink-light: #f6eedf;
    --ink-muted: #cbb48f;
    --leaf-deep: #6b4a2b;
    --leaf-warm: #a87a45;
  }
  * { margin: 0; padding: 0; box-sizing: border-box; }
  html, body { width: 1200px; height: 1015px; overflow: hidden; }
  body {
    background: var(--stage);
    display: flex;
    flex-direction: column;
    align-items: center;
    justify-content: center;
    gap: 56px;
  }
  .card {
    width: 736px;
    height: 420px;
    display: flex;
    box-shadow: 0 10px 30px rgba(0,0,0,.55);
  }
  .card__panel { height: 100%; display: flex; align-items: center; position: relative; }
  .card__panel--light { background: var(--card-light); width: 47%; }
  .card__panel--dark { background: var(--card-dark); flex: 1; }
  .card--back .card__panel--light { justify-content: flex-start; padding-left: 34px; }
  .card__panel--center { justify-content: center; }

  .leaf-band {
    position: absolute;
    top: 0;
    left: 0;
    width: 14px;
    height: 100%;
    background: linear-gradient(180deg, var(--leaf-warm), var(--leaf-deep) 55%, var(--leaf-warm));
  }

  .tagline {
    font-family: "Oswald", sans-serif;
    font-weight: 500;
    font-size: 28px;
    letter-spacing: 4px;
    white-space: nowrap;
    color: var(--ink-dark);
    text-transform: uppercase;
  }
  .wordmark {
    font-family: "Montserrat", sans-serif;
    font-weight: 800;
    font-size: 38px;
    line-height: 1.05;
    text-transform: uppercase;
    text-align: center;
    letter-spacing: 1px;
  }
  .wordmark--light { color: var(--ink-light); }
  .wordmark--dark { color: var(--ink-dark); }

  .contact {
    padding-left: 48px;
    font-family: "Arimo", sans-serif;
    color: var(--ink-light);
  }
  .contact__name { font-weight: 700; font-size: 27px; text-transform: uppercase; letter-spacing: .5px; }
  .contact__role { font-size: 20px; color: var(--ink-muted); margin-bottom: 40px; }
  .contact__list { list-style: none; }
  .contact__item { display: flex; align-items: center; gap: 8px; font-size: 21px; line-height: 1.35; }
  .contact__icon { width: 18px; height: 18px; flex: none; }
</style>
</head>
<body>

  <section class="card card--back">
    <div class="card__panel card__panel--light">
      <p class="tagline">Respect the smoke</p>
    </div>
    <div class="card__panel card__panel--dark card__panel--center">
      <div class="leaf-band" role="img" aria-label="Cigar leaf texture strip"></div>
      <p class="wordmark wordmark--light">Calden<br>Leafworks</p>
    </div>
  </section>

  <section class="card card--front">
    <div class="card__panel card__panel--light card__panel--center">
      <p class="wordmark wordmark--dark">Calden<br>Leafworks</p>
    </div>
    <div class="card__panel card__panel--dark">
      <div class="leaf-band" role="img" aria-label="Cigar leaf texture strip"></div>
      <div class="contact">
        <p class="contact__name">Kevin Oldacre</p>
        <p class="contact__role">Owner</p>
        <ul class="contact__list">
          <li class="contact__item">
            <svg class="contact__icon" viewBox="0 0 24 24" aria-hidden="true"><path fill="#f6eedf" d="M6.6 10.8a15.1 15.1 0 0 0 6.6 6.6l2.2-2.2a1 1 0 0 1 1-.25 11.4 11.4 0 0 0 3.6.57 1 1 0 0 1 1 1V20a1 1 0 0 1-1 1A17 17 0 0 1 3 4a1 1 0 0 1 1-1h3.5a1 1 0 0 1 1 1c0 1.25.2 2.45.57 3.57a1 1 0 0 1-.25 1z"/></svg>
            555-017-4863
          </li>
          <li class="contact__item">
            <svg class="contact__icon" viewBox="0 0 24 24" aria-hidden="true"><path fill="#f6eedf" d="M2 5h20v14H2z"/><path fill="none" stroke="#3a2a1f" stroke-width="1.6" d="M2.5 5.5 12 13l9.5-7.5"/></svg>
            koldacre@caldenleaf.com
          </li>
          <li class="contact__item">
            <svg class="contact__icon" viewBox="0 0 24 24" aria-hidden="true"><circle cx="12" cy="12" r="10" fill="#f6eedf"/><g fill="none" stroke="#3a2a1f" stroke-width="1.3"><ellipse cx="12" cy="12" rx="4" ry="10"/><path d="M2 12h20M4 7h16M4 17h16"/></g></svg>
            caldenleafworks.com
          </li>
        </ul>
      </div>
    </div>
  </section>

</body>
</html>
```